New Design for Willow Glow & Laser

The name of our company is Willow Glow & Laser, and this is our current website: www.WillowGlowLaser.example. We are looking for a fresh design mock-up of our website.
What is important to us?
> We want to maintain the same navigation.
> We want to use the same content (e.g., text, pictures, etc.)
> We want to maintain the color scheme.
> The website aims to get visitors to BOOK ONLINE or BUY ONLINE.
Essential instructions for designers:
> Please visit our current website and our social media accounts to get a better idea of our brand design.
> We want a mockup design for our home page, service page, pricing page, before & after page, shop deals page, careers page, contact pages, and blog pages.
> Color codes: #faa641, #222222, #fffffe, #ea8103
Target Market(s)
women 25 - 45
Number of Pages Required
5+ page

```html
<!DOCTYPE html>
<html lang="en">
<head>
<meta charset="utf-8">
<title>Willow Glow &amp; Laser</title>
<link href="https://fonts.googleapis.com/css2?family=Poppins:wght@400;500;600;700&display=swap" rel="stylesheet">
<style>
:root{
  --orange:#faa641;
  --orange-deep:#ea8103;
  --ink:#222222;
  --white:#fffffe;
  --soft:#f7f7f7;
  --muted:#555555;
  --dark:#1c1c1c;
}
*{margin:0;padding:0;box-sizing:border-box}
html,body{width:1200px;height:4320px;overflow:hidden}
body{font-family:'Poppins',sans-serif;color:var(--ink);background:var(--white);position:relative}
.abs{position:absolute}
section,header,footer{position:absolute;left:0;width:1200px;overflow:hidden}
.btn{position:absolute;display:flex;align-items:center;justify-content:center;background:var(--orange);color:var(--white);border-radius:6px;font-weight:500;text-transform:uppercase}
.center{text-align:center;width:100%}
.arrow{position:absolute;width:38px;height:38px;border-radius:50%;display:flex;align-items:center;justify-content:center}
.arrow.prev{background:var(--ink)}
.arrow.next{background:var(--orange)}
.social{display:flex;gap:5px}
.social span{width:16px;height:16px;border-radius:50%;background:var(--ink);display:block}
.photo{position:absolute}

/* top bar */
.topbar{top:0;height:37px;background:var(--white);font-size:15px}
.topbar .social{position:absolute;left:88px;top:10px}
.topbar .contact{position:absolute;right:88px;top:8px;display:flex;gap:22px;align-items:center}
.topbar .contact div{display:flex;align-items:center;gap:8px}

/* nav */
.nav{top:37px;height:101px;background:var(--white)}
.brand{position:absolute;display:flex;align-items:center;gap:10px;font-weight:700;color:var(--ink)}
.nav .brand{left:88px;top:32px;font-size:26px}
.brand .dot{width:30px;height:30px;border-radius:50%;background:var(--orange);flex-shrink:0}
.menu{position:absolute;left:452px;top:40px;display:flex;gap:26px;font-size:13px}
.menu .active{color:var(--orange);position:relative}
.menu .active::after{content:"";position:absolute;left:-8px;right:-8px;bottom:-12px;height:2px;background:var(--orange)}
.nav .btn{left:955px;top:28px;width:160px;height:45px;font-size:15px}

/* hero */
.hero{top:138px;height:628px;background:linear-gradient(100deg,#141414 0%,#2b2622 48%,#c98a3e 75%,var(--orange) 100%)}
.hero .kicker{left:86px;top:168px;font-size:62px;font-weight:700;color:var(--orange);line-height:1}
.hero h1{position:absolute;left:86px;top:248px;font-size:64px;font-weight:700;color:var(--white);line-height:1}
.hero p{position:absolute;left:86px;top:338px;font-size:18px;color:var(--white);line-height:29px}
.hero .btn{left:88px;top:437px;width:200px;height:70px;font-size:20px;text-transform:none}
.hero .ring-white{left:511px;top:-20px;width:670px;height:670px;border-radius:50%;background:var(--white)}
.hero .ring-orange{left:546px;top:15px;width:600px;height:600px;border-radius:50%;background:var(--orange)}
.hero .photo{left:575px;top:44px;width:542px;height:542px;border-radius:50%;background:radial-gradient(circle at 45% 45%,#e9c3a6,#b98465 60%,#3a3f6a 100%)}

/* offer */
.offer{top:766px;height:584px;background:var(--white)}
.section-title{position:absolute;font-weight:600;color:var(--ink)}
.offer .section-title{top:98px;font-size:40px}
.card{position:absolute;top:198px;width:246px;text-align:center}
.card .photo{position:relative;width:246px;height:159px;border-radius:12px;background:linear-gradient(135deg,#d9b9a0,#8c6d5c)}
.card h3{font-size:18px;font-weight:500;margin-top:18px}
.card p{font-size:11px;color:var(--muted);line-height:20px;margin:8px 14px 0;text-align:justify;text-align-last:center}
.card a{display:inline-block;margin-top:12px;font-size:12px;color:var(--orange);text-decoration:underline;font-weight:500}

/* about */
.about{top:1350px;height:704px;background:var(--soft)}
.about .photo{left:64px;top:90px;width:489px;height:510px;border-radius:12px;background:linear-gradient(160deg,#e8e4df,#b7a08e 60%,#5d4a40)}
.about h2{position:absolute;left:634px;top:125px;font-size:36px;font-weight:600}
.about .copy{position:absolute;left:634px;top:216px;width:482px;font-size:15px;line-height:31px;color:var(--muted)}
.about .copy p+p{margin-top:31px}
.about .btn{left:634px;top:492px;width:188px;height:58px;font-size:15px}

/* cta */
.cta{top:2054px;height:492px;background:linear-gradient(90deg,#2a2a2a,#3b3835 50%,#222)}
.cta h2{position:absolute;top:112px;font-size:48px;font-weight:600;color:var(--white)}
.cta p{position:absolute;top:192px;font-size:16px;line-height:31px;color:var(--white)}
.cta .btn{left:476px;top:306px;width:248px;height:72px;font-size:20px;border-radius:10px}

/* testimonials */
.reviews{top:2546px;height:456px;background:var(--white)}
.reviews .section-title{top:100px;font-size:42px}
.review{position:absolute;top:219px;width:360px}
.review .photo{left:0;top:0;width:90px;height:90px;border-radius:50%;background:linear-gradient(135deg,#d8d8d8,#8f8f8f)}
.review .quote{position:absolute;left:108px;top:0;width:218px;font-size:12px;line-height:20px;color:var(--muted);text-align:justify}
.review .quote b{color:var(--orange);font-size:22px;font-weight:700;margin-right:10px;line-height:10px}
.review .name{position:absolute;left:108px;top:132px;font-size:14px;font-weight:600}
.review .stars{position:absolute;left:108px;top:154px;color:#f4c20d;font-size:11px;letter-spacing:1px}

/* contact strip */
.strip{top:3002px;height:131px;background:var(--dark)}
.strip .chev{left:88px;top:44px}
.strip h3{position:absolute;left:153px;top:44px;font-size:32px;font-weight:600;color:var(--white)}
.strip .btn{left:912px;top:28px;width:200px;height:72px;font-size:20px;text-transform:uppercase}

/* gallery */
.gallery{top:3133px;height:615px;background:var(--white)}
.gallery .section-title{top:72px;font-size:52px}
.gallery .photo{top:171px;width:332px;height:293px;border-radius:12px}

/* newsletter */
.newsletter{position:absolute;left:216px;top:3673px;width:768px;height:149px;background:var(--orange);z-index:2}
.newsletter h3{position:absolute;top:22px;font-size:32px;font-weight:600;color:var(--white)}
.newsletter .field{position:absolute;left:183px;top:79px;width:400px;height:40px;background:var(--white);border-radius:20px;font-size:10px;color:var(--muted);padding:13px 26px}
.newsletter .signup{position:absolute;left:463px;top:79px;width:120px;height:40px;background:var(--ink);color:var(--white);border-radius:20px;font-size:14px;font-weight:500;display:flex;align-items:center;justify-content:center}

/* footer */
.footer{top:3748px;height:572px;background:var(--dark);color:var(--white)}
.footer .rule{position:absolute;left:88px;width:1024px;height:1px;background:var(--orange-deep)}
.footer .brand{left:168px;top:222px;font-size:32px;line-height:1.15;color:var(--white);gap:12px}
.footer .brand .dot{width:40px;height:40px}
.footer .brand .name{width:280px}
.footer .social{position:absolute;left:235px;top:355px;gap:8px}
.footer .social span{width:36px;height:36px;border:2px solid var(--orange);background:transparent}
.footer h4{position:absolute;top:160px;font-size:25px;font-weight:500}
.info{position:absolute;left:537px;display:flex;gap:28px}
.info .ico{width:38px;height:38px;border-radius:50%;background:var(--orange);display:flex;align-items:center;justify-content:center;flex-shrink:0}
.info strong{display:block;font-size:15px;font-weight:500}
.info span{font-size:15px;line-height:20px}
.links{position:absolute;left:884px;top:222px;font-size:15px;list-style:none}
.links li{display:flex;align-items:center;gap:12px;height:41px}
.links li i{width:14px;height:14px;border-radius:50%;background:var(--orange);display:block}
.legal{position:absolute;top:508px;font-size:13px}
</style>
</head>
<body>

<header class="topbar">
  <div class="social"><span></span><span></span><span></span><span></span></div>
  <div class="contact">
    <div><svg width="16" height="16" viewBox="0 0 24 24"><path d="M6.6 10.8a15 15 0 0 0 6.6 6.6l2.2-2.2a1 1 0 0 1 1-.25 11.4 11.4 0 0 0 3.6.57 1 1 0 0 1 1 1V20a1 1 0 0 1-1 1A17 17 0 0 1 3 4a1 1 0 0 1 1-1h3.5a1 1 0 0 1 1 1c0 1.25.2 2.45.57 3.57a1 1 0 0 1-.25 1z" fill="#faa641"/></svg>(555) 014-2290</div>
    <div><svg width="16" height="12" viewBox="0 0 16 12"><rect width="16" height="12" rx="1" fill="#faa641"/><path d="M0 1l8 6 8-6" stroke="#fff" stroke-width="1.4" fill="none"/></svg>hello@willowglowlaser.example</div>
  </div>
</header>

<nav class="nav">
  <div class="brand"><span class="dot"></span>Willow Glow &amp; Laser</div>
  <div class="menu">
    <span class="active">HOME</span><span>SERVICES ▾</span><span>PRICING ▾</span><span>ABOUT ▾</span><span>BLOG</span><span>CONTACT</span>
  </div>
  <div class="btn">Book Online</div>
</nav>

<section class="hero">
  <div class="abs kicker">Your skin</div>
  <h1>DESERVES IT</h1>
  <p>LASER CENTER &amp; MEDISPA located in Downtown<br>Phoenix, Tempe, Tucson, &amp; Yuma.</p>
  <div class="btn">BOOK ONLINE</div>
  <div class="abs ring-white"></div>
  <div class="abs ring-orange"></div>
  <div class="photo" role="img" aria-label="Client relaxing during a facial treatment with a glass wand device"></div>
</section>

<section class="offer">
  <h2 class="section-title center">What We Offer</h2>
  <div class="arrow prev" style="left:23px;top:343px"><svg width="12" height="12" viewBox="0 0 12 12"><path d="M8 1L3 6l5 5" stroke="#fff" stroke-width="2" fill="none"/></svg></div>
  <div class="arrow next" style="left:1138px;top:343px"><svg width="12" height="12" viewBox="0 0 12 12"><path d="M4 1l5 5-5 5" stroke="#fff" stroke-width="2" fill="none"/></svg></div>
  <article class="card" style="left:84px">
    <div class="photo" role="img" aria-label="Photofacial light treatment with protective eyewear"></div>
    <h3>Photofacials</h3>
    <p>An photofacial is a light treatment that uses an FDA-approved device to deliver an arc of light energy that penetrates all levels of the skin.</p>
    <a>READ MORE</a>
  </article>
  <article class="card" style="left:345px">
    <div class="photo" role="img" aria-label="Injection treatment on the forehead"></div>
    <h3>Lumitox Injections</h3>
    <p>Today Calmora and Lumitox are the most trusted and widely used injectable neuromodulators. Lumitox is made by Veralis Labs and Calmora</p>
    <a>READ MORE</a>
  </article>
  <article class="card" style="left:610px">
    <div class="photo" role="img" aria-label="Laser hair removal device on the underarm"></div>
    <h3>Laser Hair Removal</h3>
    <p>You go to shave your legs (or chest or, wink, wink, other body parts) right before that big date and end up bleeding like crazy</p>
    <a>READ MORE</a>
  </article>
  <article class="card" style="left:870px">
    <div class="photo" role="img" aria-label="Microneedling pen treatment on the forehead"></div>
    <h3>Microneedling</h3>
    <p>Our skin is the most valuable real estate that the human body has. It is essential that we feel comfortable and confident in our skin.</p>
    <a>READ MORE</a>
  </article>
</section>

<section class="about">
  <div class="photo" role="img" aria-label="Client checking her skin in a hand mirror"></div>
  <h2>About Willow Glow &amp; Laser</h2>
  <div class="copy">
    <p>At Willow Glow &amp; Laser, we've always believed that caring about your skin and your appearance is not selfish, it is self-care. It's time to be proud of the steps you take to look your best and it's time you ask for the best. Your skin deserves it.</p>
    <p>Willow brings to you the latest technology, techniques, and the best professionals to deliver the results you want guaranteed.</p>
  </div>
  <div class="btn">Read More</div>
</section>

<section class="cta" role="img" aria-label="Dark background with a treatment in progress">
  <h2 class="center">Get Your Treatment Right Away!</h2>
  <p class="center">Lorem ipsum dolor sit amet, consectetur adipiscing elit. Nulla convallis lectus nunc. Sed tris<br>tique quam in ligula posu ere dapibus. Cras sodales, magna nec imperdiet porta</p>
  <div class="btn">BOOK ONLINE</div>
</section>

<section class="reviews">
  <h2 class="section-title center">What Our Happy Clients Say</h2>
  <div class="arrow prev" style="left:21px;top:259px"><svg width="12" height="12" viewBox="0 0 12 12"><path d="M8 1L3 6l5 5" stroke="#fff" stroke-width="2" fill="none"/></svg></div>
  <div class="arrow next" style="left:1140px;top:259px"><svg width="12" height="12" viewBox="0 0 12 12"><path d="M4 1l5 5-5 5" stroke="#fff" stroke-width="2" fill="none"/></svg></div>
  <div class="review" style="left:87px">
    <div class="photo" role="img" aria-label="Client portrait"></div>
    <p class="quote"><b>“</b>She explained the procedure to me, answered all questions and did a great job at making me feel at ease. I would absolutely recommend Willow Glow &amp; Laser.</p>
    <div class="name">Maya R.</div><div class="stars">★★★★★</div>
  </div>
  <div class="review" style="left:440px">
    <div class="photo" role="img" aria-label="Client portrait"></div>
    <p class="quote"><b>“</b>I have been going to Willow Glow &amp; Laser for 2 years now. I am very pleased with my laser hair reduction results.</p>
    <div class="name">Lena T.</div><div class="stars">★★★★★</div>
  </div>
  <div class="review" style="left:790px">
    <div class="photo" role="img" aria-label="Client portrait"></div>
    <p class="quote"><b>“</b>Rosa is my technician and I love her! Always goes the extra mile to make sure areas are covered, and that I'm getting the best result. I couldn't be happier.</p>
    <div class="name">Clara B.</div><div class="stars">★★★★★</div>
  </div>
</section>

<section class="strip">
  <svg class="abs chev" width="52" height="44" viewBox="0 0 52 44"><path d="M4 4l18 18L4 40M26 4l18 18-18 18" stroke="#faa641" stroke-width="7" fill="none"/></svg>
  <h3>If you have any questions, please contact us.</h3>
  <div class="btn">GET IN TOUCH</div>
</section>

<section class="gallery">
  <h2 class="section-title center">Gallery</h2>
  <div class="arrow prev" style="left:20px;top:314px"><svg width="12" height="12" viewBox="0 0 12 12"><path d="M8 1L3 6l5 5" stroke="#fff" stroke-width="2" fill="none"/></svg></div>
  <div class="arrow next" style="left:1140px;top:314px"><svg width="12" height="12" viewBox="0 0 12 12"><path d="M4 1l5 5-5 5" stroke="#fff" stroke-width="2" fill="none"/></svg></div>
  <div class="photo" style="left:87px;background:linear-gradient(135deg,#f2f1ee,#9c8677)" role="img" aria-label="Client holding a hand mirror"></div>
  <div class="photo" style="left:434px;background:linear-gradient(135deg,#e6dfd6,#6f6058)" role="img" aria-label="Consultation with a tablet in the clinic"></div>
  <div class="photo" style="left:781px;background:linear-gradient(135deg,#d9d4cf,#3a3330)" role="img" aria-label="Technician treating a client in the chair"></div>
</section>

<div class="newsletter">
  <h3 class="center">Our Newsletter Sign Up</h3>
  <div class="field">Enter Email Address</div>
  <div class="signup">SIGNUP</div>
</div>

<footer class="footer">
  <div class="rule" style="top:118px"></div>
  <div class="brand"><span class="dot"></span><span class="name">Willow Glow<br>&amp; Laser</span></div>
  <div class="social"><span></span><span></span><span></span><span></span></div>
  <h4 style="left:537px">Address</h4>
  <h4 style="left:884px">Quick Links</h4>
  <div class="info" style="top:238px">
    <div class="ico"><svg width="14" height="18" viewBox="0 0 14 18"><path d="M7 0a7 7 0 0 1 7 7c0 5-7 11-7 11S0 12 0 7a7 7 0 0 1 7-7z" fill="#fff"/><circle cx="7" cy="7" r="2.6" fill="#faa641"/></svg></div>
    <div><strong>ADDRESS</strong><span>2200 N Orchard Ave Suite 150<br>Mesa Vista, AZ 85000</span></div>
  </div>
  <div class="info" style="top:326px">
    <div class="ico"><svg width="16" height="16" viewBox="0 0 24 24"><path d="M6.6 10.8a15 15 0 0 0 6.6 6.6l2.2-2.2a1 1 0 0 1 1-.25 11.4 11.4 0 0 0 3.6.57 1 1 0 0 1 1 1V20a1 1 0 0 1-1 1A17 17 0 0 1 3 4a1 1 0 0 1 1-1h3.5a1 1 0 0 1 1 1c0 1.25.2 2.45.57 3.57a1 1 0 0 1-.25 1z" fill="#fff"/></svg></div>
    <div><strong>PHONE NUMBER</strong><span>(555) 014-2290</span></div>
  </div>
  <div class="info" style="top:404px">
    <div class="ico"><svg width="16" height="12" viewBox="0 0 16 12"><rect width="16" height="12" rx="1" fill="#fff"/><path d="M0 1l8 6 8-6" stroke="#faa641" stroke-width="1.4" fill="none"/></svg></div>
    <div><strong>EMAIL US</strong><span>hello@willowglowlaser.example</span></div>
  </div>
  <ul class="links">
    <li><i></i>Services</li><li><i></i>Pricing</li><li><i></i>About</li><li><i></i>Blog</li><li><i></i>Contact</li>
  </ul>
  <div class="rule" style="top:488px"></div>
  <div class="legal" style="left:88px">© 2024 Willow Glow &amp; Laser. All Rights Reserved. – Privacy Policy • Terms &amp; Conditions</div>
  <div class="legal" style="left:714px">Medical Director: Dr. Martin Keller, NMD License #00-0000</div>
</footer>

</body>
</html>
```